lofty birch website

We need a new website for our new business division. We are a sustainable design firm specializing in servicing the needs if architects and developers. We have a staff consisting of architects, engineers, and former contractors and we understand green must make sense.

Bottomline - the only sustainable and lofty birch solutions are those thatbare good for the environment and good for our clients bottom line.

Our company is lofty birch and we will send you a copy of our logo you will see our tagline. Is simple. sustainable. solutions. The play with the periods is that we believe their are simple sustainable solutions and we want to use the words together and possible let each stand alone to accentuate their individual meaning in regards to benefit to our clients.

We want a cool splash page with nich graphics and pictures then later pages to feature projects and design ideas.

Target Market(s)

Our target customers are architects, developers, and contractors who would need assistance with the design process for a VARO project or assisatnce with a building owner who wants to make tehir facilty more environmentally friendly and save energy costs at the same tiem.

Industry/Entity Type

Environment

Requirements
Must have
• Needs a construction look with an environmentally friendly surrounding that is pleasing to look at. Must appeal to the client not only as environmentally friendly but also a wise investment.
Nice to have
• Opportunity for a connection to Social networking including a blog.
Should not have
• A totally environmental building feel at whatever cost. We want to emphasize that it is possible to build environmental friendly and save you money over the life of your building

```html
<!DOCTYPE html>
<html lang="en">
<head>
<meta charset="utf-8">
<title>lofty birch — simple. sustainable. solutions.</title>
<link rel="stylesheet" href="https://fonts.googleapis.com/css2?family=Arimo:wght@400;700&display=swap">
<style>
  :root {
    --green-deep: #3f8f06;
    --green-mid: #5fae12;
    --green-active: #22c51a;
    --band-top: #2e9a12;
    --band-bottom: #16700a;
    --panel: rgba(170, 225, 110, 0.35);
    --black: #0d0d0d;
    --charcoal: #2a2a2a;
    --white: #ffffff;
    --brand-ink: #3d7f12;
    --brand-dot: #4aa51c;
  }
  * { box-sizing: border-box; margin: 0; padding: 0; }
  html, body { width: 1200px; height: 768px; overflow: hidden; }
  body {
    position: relative;
    font-family: "Arimo", Arial, sans-serif;
    color: var(--white);
    background:
      radial-gradient(ellipse 520px 260px at 780px 640px, rgba(200,245,120,0.45), transparent 70%),
      linear-gradient(160deg, var(--green-mid) 0%, var(--green-deep) 45%, var(--green-mid) 70%, var(--green-deep) 100%);
  }
  .site-header { position: absolute; inset: 0 0 auto 0; height: 114px; }
  .brand {
    position: absolute; left: 44px; top: 0; width: 416px; height: 106px;
    background: linear-gradient(180deg, #ffffff 0%, #eef7e2 100%);
    border-radius: 0 0 12px 12px;
    display: flex; align-items: center; padding-left: 26px;
  }
  .brand-dot {
    width: 56px; height: 56px; border-radius: 50%;
    background: var(--brand-dot); margin-right: 18px; flex: none;
  }
  .brand-name {
    font-family: "Arimo", Arial, sans-serif; font-weight: 700;
    font-size: 40px; line-height: 44px; color: var(--brand-ink);
  }
  .leaf-art {
    position: absolute; left: 860px; top: 0; width: 300px; height: 195px;
    background: radial-gradient(ellipse at 55% 40%, #7fd33a 0%, #3c9a12 60%, rgba(60,154,18,0) 100%);
    border-radius: 0 0 60% 70%;
  }
  .search {
    position: absolute; left: 939px; top: 64px; width: 221px; height: 31px;
    background: var(--black); border-radius: 10px;
    font-size: 14px; line-height: 31px; padding-left: 14px; color: var(--white);
  }
  .main-nav {
    position: absolute; left: 45px; top: 114px; width: 1113px; height: 41px;
    background: linear-gradient(180deg, #2b2b2b 0%, #0a0a0a 100%);
    display: flex; font-weight: 700; font-size: 15px; line-height: 41px;
  }
  .main-nav a { color: var(--white); text-decoration: none; text-align: center; }
  .main-nav .is-active { background: linear-gradient(180deg, #3be02e 0%, var(--green-active) 100%); }
  .hero { position: absolute; left: 45px; top: 155px; width: 1113px; height: 356px; display: flex; }
  .hero-photo { height: 100%; }
  .hero-photo--loft {
    width: 537px;
    background: linear-gradient(180deg, #d9d9d4 0%, #b9b4aa 55%, #6e5a48 100%);
  }
  .hero-photo--lounge {
    width: 576px;
    background: linear-gradient(180deg, #e6e6e2 0%, #cfcac0 55%, #efefeb 100%);
  }
  .tagline-band {
    position: absolute; left: 45px; top: 511px; width: 1113px; height: 40px;
    background: linear-gradient(180deg, var(--band-top) 0%, var(--band-bottom) 100%);
    font-weight: 700; font-size: 23px; line-height: 40px;
  }
  .tagline-band span { position: absolute; top: 0; }
  .welcome {
    position: absolute; left: 45px; top: 551px; width: 1113px; height: 162px;
    background: var(--panel);
  }
  .welcome h1 {
    position: absolute; left: 24px; top: 8px;
    font-size: 32px; font-weight: 700; line-height: 38px;
  }
  .welcome p {
    position: absolute; left: 26px; width: 1030px;
    font-size: 15px; line-height: 17px;
  }
  .site-footer {
    position: absolute; left: 0; top: 713px; width: 1200px; height: 55px;
    background: linear-gradient(180deg, var(--charcoal) 0%, var(--black) 100%);
    font-size: 14px; line-height: 40px; padding-left: 46px;
  }
</style>
</head>
<body>
  <header class="site-header">
    <div class="brand">
      <span class="brand-dot"></span>
      <span class="brand-name">lofty birch</span>
    </div>
    <div class="leaf-art" role="img" aria-label="Fresh green leaves reaching down from the top corner"></div>
    <div class="search">Search</div>
  </header>

  <nav class="main-nav">
    <a href="#" style="width:108px">HOME</a>
    <a href="#" class="is-active" style="width:138px">ABOUT US</a>
    <a href="#" style="width:140px">OUR SERVICES</a>
    <a href="#" style="width:156px">OUR CLIENT</a>
    <a href="#" style="width:90px">FAQ</a>
    <a href="#" style="width:150px">CONTACT US</a>
  </nav>

  <section class="hero">
    <div class="hero-photo hero-photo--loft" role="img" aria-label="Bright loft living room with tall windows, grey sofa and wooden floor"></div>
    <div class="hero-photo hero-photo--lounge" role="img" aria-label="Modern white lounge with cream sofas, dark coffee table and striped wall"></div>
  </section>

  <div class="tagline-band">
    <span style="left:265px">SIMPLE</span>
    <span style="left:400px">•</span>
    <span style="left:450px">SUSTAINABLE</span>
    <span style="left:665px">•</span>
    <span style="left:708px">SOLUTIONS</span>
  </div>

  <main class="welcome">
    <h1>Welcome to Our Website</h1>
    <p style="top:60px">Lorem ipsum dolor sit amet, consectetur adipiscing elit. Vestibulum vitae libero et ligula consequat ullamcorper eget vel purus. Proin pellentesque sapien magna. Mauris venenatis tortor non purus facilisis dignissim. Nunc quis lectus sit amet ante luctus congue sit amet non mauris.</p>
    <p style="top:114px">Etiam a sem leo, a pellentesque nisl. Fusce sit amet ultricies ante. Aliquam erat volutpat. Aenean in mauris arcu, quis vehicula augue. Nam lacinia condimentum sapien id suscipit.</p>
  </main>

  <footer class="site-footer">Footer Text Here</footer>
</body>
</html>
```